Briloran Clear Springs needs a new business card design (we produce and sell pure bottled water)

We need a clean modern design for our new business cards, We have an existing logo which ultimately cannot be changed, however it could be slighty improved and the colours adjusted. We have this existing logo on all of our bottles, vehicles etc.

Our company slogan is "Clear from spring to every sip".
Along with our relevant company information
(Address, phone, website email etc) we will only be using names and not putting position titles for flexibilty.

We are looking for a clean, minimalist modern design.

You can view our website (if need of an update also!) to see our business.

Industry/Entity Type

Business

Contact Information for Business Card

Staff Name : XXXXXX XXXXXX
Address : 9/41 Tavenor St
Halden Rise QLD 4172
Staff Mobile Number : 04XX XXX XXX
Office Phone Number : 07 3918 2457
Staff Email Address : XXXX@brilorancleargo.com.au
Website : www.brilorancleargo.com.au

Font styles to use
Sans Serif

Colors
cee9f5
33a6d7
0492cd
0455a3
3276b5
85abd2
cedeed

Requirements
Must have
• The ability to edit and change the staff members details as we will need to edit for each respective staff member (7 in total)

```html
<!DOCTYPE html>
<html lang="en">
<head>
<meta charset="utf-8">
<title>Briloran Clear Springs – Business Card</title>
<link rel="stylesheet" href="https://fonts.googleapis.com/css2?family=Source+Sans+3:wght@400;600;700&display=swap">
<style>
  :root {
    --backdrop-top: #2b2b2b;
    --backdrop-bottom: #040404;
    --card-white: #ffffff;
    --brand-navy: #14148f;
    --brand-deep: #1a1a8c;
    --brand-soft: #3c3cb8;
    --text-body: #333333;
    --text-light: #ffffff;
  }
  html, body {
    margin: 0;
    padding: 0;
    width: 1200px;
    height: 900px;
    overflow: hidden;
  }
  body {
    position: relative;
    background: linear-gradient(180deg, var(--backdrop-top) 0%, #141414 60%, var(--backdrop-bottom) 100%);
    font-family: "Source Sans 3", Arial, sans-serif;
  }
  .card {
    position: absolute;
    top: 306px;
    width: 439px;
    height: 271px;
    border-radius: 12px;
    box-sizing: border-box;
  }
  .card--front {
    left: 149px;
    background: var(--card-white);
  }
  .card--back {
    left: 609px;
    background: var(--brand-navy);
  }
  .brand-lockup {
    position: absolute;
    left: 40px;
    top: 150px;
    display: flex;
    align-items: center;
    gap: 8px;
  }
  .brand-lockup__dot {
    width: 12px;
    height: 12px;
    border-radius: 50%;
    background: var(--brand-deep);
    flex: none;
  }
  .brand-lockup__name {
    font-weight: 700;
    font-size: 20px;
    line-height: 1.05;
    color: var(--brand-deep);
    margin: 0;
  }
  .staff {
    position: absolute;
    left: 211px;
    top: 61px;
  }
  .staff__name {
    margin: 0 0 18px;
    font-size: 16px;
    line-height: 20px;
    font-weight: 600;
    color: var(--brand-deep);
  }
  .staff__address {
    margin: 0 0 12px;
    font-size: 13px;
    line-height: 16px;
    color: var(--text-body);
    font-style: normal;
  }
  .contact-list {
    list-style: none;
    margin: 0;
    padding: 0;
  }
  .contact-list__item {
    display: flex;
    align-items: center;
    gap: 6px;
    font-size: 13px;
    line-height: 16px;
    color: var(--text-body);
  }
  .contact-list__icon {
    width: 10px;
    height: 10px;
    flex: none;
    fill: var(--brand-deep);
  }
  .back-brand {
    position: absolute;
    left: 0;
    right: 0;
    top: 128px;
    text-align: center;
    font-weight: 700;
    font-size: 26px;
    line-height: 1;
    color: var(--brand-soft);
    margin: 0;
  }
  .slogan {
    position: absolute;
    left: 0;
    right: 0;
    top: 219px;
    margin: 0;
    text-align: center;
    font-size: 14px;
    line-height: 18px;
    font-weight: 600;
    color: var(--text-light);
  }
</style>
</head>
<body>
  <section class="card card--front">
    <div class="brand-lockup">
      <span class="brand-lockup__dot"></span>
      <p class="brand-lockup__name">Briloran<br>Clear Springs</p>
    </div>
    <div class="staff">
      <h1 class="staff__name">Corvin Ashdale</h1>
      <address class="staff__address">9/41 Tavenor St<br>Halden Rise QLD 4172</address>
      <ul class="contact-list">
        <li class="contact-list__item">
          <svg class="contact-list__icon" viewBox="0 0 10 10"><rect x="2.5" y="0.5" width="5" height="9" rx="1" fill="none" stroke="#1a1a8c" stroke-width="1.2"/></svg>
          0400 587 219
        </li>
        <li class="contact-list__item">
          <svg class="contact-list__icon" viewBox="0 0 10 10"><path d="M2 0.5 L3.8 2.6 L2.8 3.8 Q4 6.2 6.2 7.2 L7.4 6.2 L9.5 8 L8.3 9.5 Q3.5 9 0.5 1.7 Z"/></svg>
          07 3918 2457
        </li>
        <li class="contact-list__item">
          <svg class="contact-list__icon" viewBox="0 0 10 10"><rect x="0.5" y="2" width="9" height="6.5"/><path d="M0.5 2 L5 5.5 L9.5 2" fill="none" stroke="#fff" stroke-width="0.9"/></svg>
          info@brilorancleargo.com.au
        </li>
        <li class="contact-list__item">
          <svg class="contact-list__icon" viewBox="0 0 10 10"><circle cx="5" cy="5" r="4.5"/><path d="M0.5 5 H9.5 M5 0.5 Q2.5 5 5 9.5 M5 0.5 Q7.5 5 5 9.5" fill="none" stroke="#fff" stroke-width="0.7"/></svg>
          www.brilorancleargo.com.au
        </li>
      </ul>
    </div>
  </section>

  <section class="card card--back">
    <p class="back-brand">Briloran<br>Clear Springs</p>
    <p class="slogan">CLEAR FROM SPRING TO EVERY SIP</p>
  </section>
</body>
</html>
```